Business Card and Simple Logo Desgin

New Zealand based start up company "Vesta Advisory LTD" requires business cards and simple logo design.

Card Content.

Vesta Advisory LTD

Rebecca Thornbury
CA, BMS (Hons)

r.thornbury@vestaadvisory.co.nz
PH +64 21 574 613

Target Market(s)

Corporate Business in IT, Finance and accounting.

Industry/Entity Type

Business

```html
<!DOCTYPE html>
<html lang="en">
<head>
<meta charset="utf-8">
<title>Vesta Advisory LTD — Business Card</title>
<link rel="stylesheet" href="https://fonts.googleapis.com/css2?family=Questrial&display=swap">
<style>
  :root {
    --backdrop: #2a2a2a;
    --card-top: #2b2b2b;
    --card-bottom: #050505;
    --brand-white: #ffffff;
    --brand-blue: #1e8fe0;
    --contact-grey: #6f6f6f;
    --divider-light: #9a9a9a;
    --divider-dark: #4a4a4a;
    --band-white: #ffffff;
    --band-text: #111111;
  }
  html, body {
    margin: 0;
    padding: 0;
    width: 1200px;
    height: 900px;
    overflow: hidden;
    background: var(--backdrop);
  }
  .canvas {
    position: relative;
    width: 1200px;
    height: 900px;
  }
  .business-card {
    position: absolute;
    left: 150px;
    top: 190px;
    width: 900px;
    height: 520px;
    overflow: hidden;
    background: linear-gradient(200deg, var(--card-top) 0%, #141414 45%, var(--card-bottom) 100%);
    box-shadow: 0 20px 50px rgba(0, 0, 0, 0.6);
    font-family: "Questrial", "Century Gothic", sans-serif;
  }
  .bokeh-field {
    position: absolute;
    left: 0;
    right: 0;
    bottom: 62px;
    height: 220px;
    background:
      radial-gradient(ellipse 60% 90% at 75% 100%, rgba(120, 120, 120, 0.22), transparent 70%),
      radial-gradient(ellipse 35% 80% at 10% 100%, rgba(110, 110, 110, 0.18), transparent 70%);
  }
  .brand {
    position: absolute;
    left: 105px;
    top: 172px;
    display: flex;
    align-items: center;
    gap: 14px;
  }
  .brand-dot {
    width: 16px;
    height: 16px;
    border-radius: 50%;
    background: var(--brand-blue);
  }
  .brand-name {
    margin: 0;
    font-size: 40px;
    font-weight: 400;
    color: var(--brand-white);
    letter-spacing: 0.5px;
  }
  .divider {
    position: absolute;
    left: 485px;
    top: 95px;
    width: 4px;
    height: 160px;
    background: linear-gradient(to bottom, var(--divider-light), var(--divider-dark));
  }
  .contact {
    position: absolute;
    left: 540px;
    top: 110px;
    color: var(--contact-grey);
  }
  .contact-name {
    margin: 0;
    font-size: 26px;
    font-weight: 400;
    line-height: 1.05;
  }
  .contact-title {
    margin: 0 0 30px;
    font-size: 26px;
    line-height: 1.05;
  }
  .contact-line {
    margin: 0;
    font-size: 19px;
    line-height: 1.35;
  }
  .web-band {
    position: absolute;
    left: 0;
    right: 0;
    bottom: 0;
    height: 62px;
    background: var(--band-white);
    display: flex;
    align-items: center;
    justify-content: center;
    padding-left: 110px;
    box-sizing: border-box;
  }
  .web-address {
    font-size: 26px;
    color: var(--band-text);
    letter-spacing: 0.3px;
  }
</style>
</head>
<body>
  <main class="canvas">
    <section class="business-card">
      <div class="bokeh-field" role="img" aria-label="Soft grey bokeh circles across the lower part of the card"></div>

      <div class="brand">
        <span class="brand-dot"></span>
        <h1 class="brand-name">Vesta Advisory LTD</h1>
      </div>

      <div class="divider"></div>

      <div class="contact">
        <h2 class="contact-name">Rebecca Thornbury</h2>
        <p class="contact-title">CA, BMS (Hons)</p>
        <p class="contact-line">r.thornbury@vestaadvisory.co.nz</p>
        <p class="contact-line">PH +64 21 574 613</p>
      </div>

      <div class="web-band">
        <span class="web-address">www.vestaadvisoryltd.com.au</span>
      </div>
    </section>
  </main>
</body>
</html>
```